The Copper Kite Website Redesign

I want a new design and website for www.thecopperkitebrookvale.com where part of the home page includes our daily specials from our POS Toast to be pulled from API. I have included photos and links to give you a better feel for the style of our restaurant.

Coding

Coded - Design and coding required

```html
<!DOCTYPE html>
<html lang="en">
<head>
<meta charset="utf-8">
<title>The Copper Kite – A Finer Diner</title>
<link href="https://fonts.googleapis.com/css2?family=Londrina+Solid:wght@400;900&family=Kalam:wght@700&family=Poppins:wght@400;500;600;700&display=swap" rel="stylesheet">
<style>
:root{
  --red:#e12a2a;
  --red-dark:#c81f1f;
  --ink:#161616;
  --dark:#1b1b1b;
  --pink:#f7dede;
  --white:#ffffff;
  --grey:#6b6b6b;
  --light:#d9d9d9;
}
*{margin:0;padding:0;box-sizing:border-box}
html,body{width:1200px;height:4275px;overflow:hidden}
body{position:relative;font-family:"Poppins",sans-serif;color:var(--ink);background:var(--white)}
.abs{position:absolute}
.center{left:0;width:1200px;text-align:center}
.script{font-family:"Kalam",cursive;color:var(--red);font-weight:700}
.display{font-family:"Londrina Solid",sans-serif;font-weight:900;letter-spacing:-1px}
.logo{font-family:"Poppins",sans-serif;font-weight:700;color:var(--red);white-space:nowrap}
.arrow{width:34px;height:34px;border-radius:50%;display:flex;align-items:center;justify-content:center;font-size:15px;font-weight:700}
.arrow.light{background:var(--white);color:var(--ink)}
.arrow.red{background:var(--red);color:var(--white)}
.btn{background:var(--red);color:var(--white);border-radius:24px;font-size:12px;font-weight:600;display:flex;align-items:center;justify-content:center;gap:6px}
.btn .dot{width:11px;height:11px;border-radius:50%;background:var(--white);color:var(--red);font-size:8px;display:flex;align-items:center;justify-content:center}

/* hero */
.hero{top:0;left:0;width:1200px;height:500px;background:linear-gradient(180deg,#1e1614,#3a2420 60%,#24160f)}
.pink-band{top:300px;left:0;width:1200px;height:1136px}
.nav{top:32px;left:556px;display:flex;gap:19px;font-size:12px;font-weight:600;color:var(--white)}
.nav .active{color:var(--red)}
.nav-icons{top:27px;left:981px;display:flex;gap:6px}
.nav-icons span{width:31px;height:31px;border-radius:50%;background:var(--white);display:flex;align-items:center;justify-content:center}
.plate{left:283px;top:335px;width:598px;height:228px;border-radius:50%;background:radial-gradient(ellipse at 50% 45%,#b8862e 0%,#6a4a25 35%,#2a2a2a 62%,#111 100%);box-shadow:0 40px 40px -20px rgba(0,0,0,.25)}

/* specials */
.dish{border-radius:50%}
.dish-side{width:342px;height:342px;border:6px solid var(--red)}
.dish-main{width:376px;height:376px;border:6px solid var(--white);box-shadow:0 0 0 2px #eee}
.dish-name{font-size:15px;font-weight:500;text-align:center}
.dish-price{font-size:25px;font-weight:600;color:var(--red);text-align:center}

/* about */
.about-text{left:617px;top:1658px;width:452px;font-size:12px;line-height:21.5px;color:var(--grey)}

/* menu */
.menu{top:2030px;left:0;width:1200px;height:1127px;background:radial-gradient(ellipse at 50% 40%,#2a2a2a,#121212)}
.tabs{top:2266px;left:139px;width:940px;height:68px;border:1px solid #3a3a3a;border-radius:6px;display:flex;align-items:center;padding-left:15px;gap:0}
.tab{color:var(--white);font-size:13.5px;font-weight:600;padding:9px 14px;margin-right:34px}
.tab.on{background:var(--red);border-radius:3px}
.item-img{width:150px;height:150px;border-radius:50%}
.item-title{font-size:16px;font-weight:600;color:var(--white)}
.item-desc{font-size:14px;line-height:25px;color:var(--light);width:315px}
.item-price{font-size:21px;font-weight:600;color:var(--red)}

/* testimonials */
.quote{left:205px;top:3558px;width:790px;text-align:center;font-size:12.5px;line-height:22px;color:var(--grey)}

/* footer */
.footer{top:3834px;left:0;width:1200px;height:441px;background:radial-gradient(ellipse at 50% 60%,#262626,#111)}
.gift{top:3695px;left:163px;width:879px;height:257px;background:var(--red);border-radius:4px}
.foot-nav{top:4138px;left:0;width:1200px;display:flex;justify-content:center;gap:19px;font-size:12.5px;font-weight:600;color:var(--white)}
.socials{top:4171px;left:548px;display:flex;gap:8px}
.socials span{width:31px;height:31px;border-radius:50%;background:var(--white)}
.copy{top:4230px;font-size:12.5px;color:var(--white)}
</style>
</head>
<body>

<!-- Hero -->
<div class="abs hero" role="img" aria-label="Dimly lit diner interior, blurred"></div>
<svg class="abs pink-band" width="1200" height="1136" viewBox="0 0 1200 1136" aria-hidden="true">
  <path d="M0 140 Q600 -40 1200 140 L1200 1136 L0 1136 Z" fill="#f7dede"/>
</svg>

<div class="abs logo" style="left:120px;top:40px;font-size:40px">The Copper Kite</div>
<nav class="abs nav">
  <span class="active">HOME</span><span>ABOUT US</span><span>MENU</span><span>RETAIL</span><span>PRESS</span><span>CONTACT US</span>
</nav>
<div class="abs nav-icons">
  <span><svg width="13" height="13" viewBox="0 0 14 14"><circle cx="6" cy="6" r="4" fill="none" stroke="#161616" stroke-width="2"/><path d="M9 9l4 4" stroke="#161616" stroke-width="2"/></svg></span>
  <span><svg width="13" height="13" viewBox="0 0 14 14"><circle cx="7" cy="4.5" r="3" fill="#161616"/><path d="M1.5 13a5.5 5 0 0 1 11 0z" fill="#161616"/></svg></span>
  <span><svg width="13" height="13" viewBox="0 0 14 14"><path d="M1 2h2l2 7h7l1.5-5H4" fill="none" stroke="#161616" stroke-width="1.8"/><circle cx="6" cy="12" r="1.2" fill="#161616"/><circle cx="11" cy="12" r="1.2" fill="#161616"/></svg></span>
</div>

<div class="abs center display" style="top:142px;font-size:32px;color:var(--white);font-weight:400;letter-spacing:0">TASTE THE EXTRAORDINARY</div>
<div class="abs center display" style="top:200px;font-size:92px;color:var(--white);line-height:1">Our Special Dish Awaits You!</div>
<div class="abs arrow light" style="left:68px;top:286px">«</div>
<div class="abs arrow red" style="left:1097px;top:286px">»</div>
<div class="abs plate" role="img" aria-label="Black plate with scrambled eggs, greens, roasted potatoes and a fried egg"></div>

<!-- Specials -->
<div class="abs center script" style="top:680px;font-size:33px">OUR SPECIAL</div>
<div class="abs center display" style="top:725px;font-size:66px">BEST FOODS</div>

<div class="abs dish dish-side" style="left:111px;top:875px;background:radial-gradient(circle at 40% 55%,#e0a24a,#b0652a 60%,#7a3f1d)" role="img" aria-label="Crispy egg rolls with red dipping sauce"></div>
<div class="abs dish dish-side" style="left:747px;top:875px;background:radial-gradient(circle at 50% 55%,#e9d8a6,#b9a25a 55%,#5f7a2e)" role="img" aria-label="Stuffed chicken roll with broccoli and cream sauce"></div>
<div class="abs dish dish-main" style="left:411px;top:833px;background:radial-gradient(circle at 50% 55%,#c9883c,#6c4320 55%,#2b3a5a)" role="img" aria-label="Stacked cheeseburger on a diner counter"></div>
<div class="abs arrow light" style="left:68px;top:1049px">«</div>
<div class="abs arrow red" style="left:1097px;top:1049px">»</div>

<div class="abs dish-name" style="left:132px;top:1243px;width:300px">EGGS ALA BORING</div>
<div class="abs dish-price" style="left:132px;top:1272px;width:300px">$12.95</div>
<div class="abs dish-name" style="left:449px;top:1238px;width:300px;font-size:16px">CHICKEN WITH BURGER</div>
<div class="abs" style="left:464px;top:1265px;width:270px;text-align:center;font-size:12px;line-height:20px;color:var(--grey)">Lorem ipsum dolor sit amet, consectetur adipiscing elit, sed do eiusmod</div>
<div class="abs dish-price" style="left:449px;top:1320px;width:300px;font-size:28px">$ 18.00</div>
<div class="abs dish-name" style="left:761px;top:1243px;width:300px">GREEN EGGS AND HAM</div>
<div class="abs dish-price" style="left:761px;top:1272px;width:300px">$13.95</div>

<!-- About -->
<svg class="abs" style="left:120px;top:1515px" width="434" height="424" viewBox="0 0 434 424" aria-hidden="true">
  <circle cx="222" cy="212" r="208" fill="#e12a2a"/>
</svg>
<div class="abs dish" style="left:120px;top:1519px;width:416px;height:416px;background:linear-gradient(180deg,#d9c24a 0%,#e8d55a 35%,#e9e2d8 50%,#4a5c9a 75%,#2d3b6d 100%)" role="img" aria-label="Restaurant storefront with yellow tiled wall and sign"></div>
<div class="abs script" style="left:617px;top:1534px;font-size:33px">ABOUT US</div>
<div class="abs display" style="left:617px;top:1575px;font-size:70px">OUR RESTAURANT</div>
<p class="abs about-text">The doors of The Copper Kite: a finer diner were eagerly thrown open for the first time on December 28th 2004. We welcomed our first customers and started our magnificent life as a business that continues on through today. Along with our beloved and inquisitive customers came the many questions of our origin. The most important of which we will address right here and now... "Why?" they asked "Why did you name your restaurant The Copper Kite?" We always swore we would make up some exciting folklore tale of the origin of our now-venerated name, but we never quite came up with a story glorious enough to do justice.</p>
<div class="abs btn" style="left:617px;top:1875px;width:148px;height:44px">LEARN MORE <span class="dot">›</span></div>

<!-- Menu -->
<div class="abs menu"></div>
<div class="abs center script" style="top:2105px;font-size:33px">OUR MENU</div>
<div class="abs center display" style="top:2145px;font-size:66px;color:var(--white)">BEST FOODS</div>
<div class="abs tabs">
  <span class="tab on">ALL THINGS EGGS</span><span class="tab">SUGAR SHACK</span><span class="tab">GREEN THINGS</span><span class="tab">BETWEEN BREAD</span><span class="tab">OTHER STUFF</span>
</div>
<div class="abs" style="left:999px;top:2290px;width:19px;height:19px;border-radius:50%;background:var(--red);color:#fff;font-size:11px;text-align:center;line-height:19px">‹</div>
<div class="abs" style="left:1025px;top:2290px;width:19px;height:19px;border-radius:50%;background:#fff;color:#111;font-size:11px;text-align:center;line-height:19px">›</div>

<div class="abs item-img" style="left:86px;top:2405px;background:radial-gradient(circle,#f2c13a,#d96a2a 55%,#7b3b1c)" role="img" aria-label="Open-face eggs and ham with fried egg"></div>
<div class="abs item-title" style="left:271px;top:2407px">GREEN EGGS AND HAM</div>
<div class="abs item-desc" style="left:271px;top:2441px">Poblano Pesto and Jack Cheese Rumbled with Eggs Sidled by Seared City Ham</div>
<div class="abs item-price" style="left:271px;top:2522px">$13.95</div>

<div class="abs item-img" style="left:617px;top:2405px;background:radial-gradient(circle,#e2c47a,#9a7a3a 55%,#4b3a1a)" role="img" aria-label="Egg wraps with vegetables"></div>
<div class="abs item-title" style="left:802px;top:2407px">VEGGIE RUMBLE</div>
<div class="abs item-desc" style="left:802px;top:2441px;width:320px">Marcello's Fave - a Rumble of Eggs with Fresh Mozzarella, Basil, Tomatoes, &amp; Green Olives</div>
<div class="abs item-price" style="left:802px;top:2522px">$12.95</div>

<div class="abs item-img" style="left:86px;top:2604px;background:radial-gradient(circle,#f3d870,#c99a35 55%,#5a3d1a)" role="img" aria-label="Rolled omelette slices"></div>
<div class="abs item-title" style="left:271px;top:2606px">THE BOOT</div>
<div class="abs item-desc" style="left:271px;top:2641px">Poblano Pesto and Jack Cheese Rumbled with Eggs Sidled by Seared City Ham</div>
<div class="abs item-price" style="left:271px;top:2721px">$12.95</div>

<div class="abs item-img" style="left:617px;top:2604px;background:radial-gradient(circle,#e7b45a,#b3452a 55%,#4a2418)" role="img" aria-label="Toasted wraps with mushrooms and greens"></div>
<div class="abs item-title" style="left:802px;top:2606px">THE FORAGER</div>
<div class="abs item-desc" style="left:802px;top:2641px;width:320px">Mushrooms, Caramelized Onion, Smoked Gouda &amp; Greens Rumbled with Eggs</div>
<div class="abs item-price" style="left:802px;top:2721px">$13.95</div>

<div class="abs item-img" style="left:86px;top:2803px;background:radial-gradient(circle,#c9d66a,#c88a3a 55%,#4a3220)" role="img" aria-label="Egg sandwich on a croissant"></div>
<div class="abs item-title" style="left:271px;top:2806px">HUEVOS RANCHEROS</div>
<div class="abs item-desc" style="left:271px;top:2840px">Marcello's Fave - a Rumble of Eggs with Fresh Mozzarella, Basil, Tomatoes, &amp; Green Olives</div>
<div class="abs item-price" style="left:271px;top:2920px">$12.95</div>

<div class="abs item-img" style="left:617px;top:2803px;background:radial-gradient(circle,#f0c04a,#c8402a 55%,#4a2418)" role="img" aria-label="Steak and egg sandwich"></div>
<div class="abs item-title" style="left:802px;top:2806px">COWBOY CARVER</div>
<div class="abs item-desc" style="left:802px;top:2840px;width:330px">Seared Flank Steak Straddlin' a Wildwest Sauce, Two Eggs Fried Easy to Hard &amp; Yippee Kayay...Pick Your Toast</div>
<div class="abs item-price" style="left:802px;top:2920px">$17.95</div>

<div class="abs btn" style="left:526px;top:3021px;width:148px;height:44px">VIEW MORE <span class="dot">›</span></div>

<!-- Testimonials -->
<div class="abs center script" style="top:3236px;font-size:33px">CLIENT SAY'S</div>
<div class="abs center display" style="top:3277px;font-size:66px">OUR TESTIMONIALS</div>
<div class="abs dish" style="left:533px;top:3380px;width:132px;height:132px;background:radial-gradient(circle at 50% 40%,#f1c9a6,#e8b48c 60%,#d9a07a)" role="img" aria-label="Customer portrait"></div>
<div class="abs center" style="top:3531px;font-size:15px;font-weight:600;color:var(--red)">MARA ELLIS</div>
<p class="abs quote">Lorem ipsum dolor sit amet, consectetur adipiscing elit, sed do eiusmod tempor incididunt ut labore et dolore magna aliqua. Ut enim ad minim veniam, quis nostrud exercitation ullamco laboris nisi ut aliquip ex ea commodo consequat. Duis aute irure dolor in reprehenderit in voluptate velit esse cillum dolore eu fugiat n</p>
<div class="abs arrow light" style="left:68px;top:3540px;box-shadow:0 0 0 1px #eee">«</div>
<div class="abs arrow red" style="left:1097px;top:3540px">»</div>

<!-- Footer -->
<div class="abs footer"></div>
<div class="abs gift"></div>
<div class="abs display" style="left:207px;top:3748px;font-size:48px;color:var(--white);font-weight:400">GIFT CARDS</div>
<div class="abs" style="left:207px;top:3823px;font-size:20px;line-height:32px;font-weight:500;color:var(--white)">GIFT CARDS ARE AVAILABLE FOR PURCHASE<br>AT THE COPPER KITE IN ANY DENOMINATION!</div>
<div class="abs dish" style="left:794px;top:3659px;width:258px;height:258px;background:radial-gradient(circle,#f4c53a 0%,#f5f0e6 30%,#e9e4dc 70%,#cfc8bd)" role="img" aria-label="White plate with fried egg and tomatoes"></div>
<div class="abs" style="left:714px;top:3831px;width:262px;height:115px;border-radius:6px;background:linear-gradient(135deg,#b91c1c 0 18%,#f3f1ee 18%)" role="img" aria-label="Gift card wrapped with a red ribbon"></div>

<div class="abs center" style="top:4020px"><span class="logo" style="font-size:46px">The Copper Kite</span></div>
<nav class="abs foot-nav"><span>HOME</span><span>ABOUT US</span><span>MENU</span><span>RETAIL</span><span>PRESS</span><span>CONTACT US</span></nav>
<div class="abs socials"><span></span><span></span><span></span></div>
<div class="abs center copy">Copyright@2025 - All Rights Reserved</div>

</body>
</html>
```